Exciting new website for concierge aesthetic company

Simple, elegant, fresh design for female owned concierge aesthetic company, catering to both men and women ages 30-60. We would like a home page with an exciting catch phrase, a brief description of the company and a section to fill out an appointment request that includes a section for a referral. Please also have a book appointment link in the header of all pages that will link back to booking information form on home page. Separate pages to include:
- Services = 3 different services. Each service stating the name of the service and then providing a brief description. 3 services are "Private Session" for 1 client, "Group Session" for 2-5 clients, "Party" for 6+ clients. Will provide service descriptions text later. Item at bottom of page to allow description of how to "Host a Party".
- Products = 4 different product lines. Will provide pictures of product, brief description and link to manufacturer's website.
- Stories = brief client reviews to include before and after photos
- About us = Personal picture with brief description of owner's fun, exciting and family focussed lifestyle.
*Our domain is registered with varnix and we be using varnix for website hosting.

Target Market(s)

30-60 year old men and women, but mostly women

Industry/Entity Type

beauty and aesthetics

Coding

Coded - Design and coding required

Number of Pages Required

5+ page

Font styles to use
Sans Serif
Script

Colors
59FF00
82FF00
B8FF75
E3FFCB
F4FFEA
FFC000
F8CF3A
FAE287
FDF2CF
FEFAEE
F0912C
F2A743
F7CA91
FBE8D2
FDF5EE
E54698
E96AAD
F1A4CE
F9D9EA
FCEFF6

Requirements
Must have
• coded for varnix
Should not have
• corny pictures. No needles in pictures or graphics. No medical office or medical chair in pictures.

```html
<!DOCTYPE html>
<html lang="en">
<head>
<meta charset="utf-8">
<title>Velvet Muse Concierge Aesthetics</title>
<link rel="stylesheet" href="https://fonts.googleapis.com/css2?family=Dancing+Script:wght@500;600&family=Raleway:wght@400;500;600&display=swap">
<style>
:root{
  --pink:#E0338A;
  --pink-soft:#E96AAD;
  --pink-pale:#FCEFF6;
  --pink-blush:#F9D9EA;
  --orange:#F0912C;
  --orange-deep:#E8702A;
  --peach:#FBE8D2;
  --peach-pale:#FDF5EE;
  --ink:#333;
  --muted:#777;
  --hero-bg:#ECE6E3;
}
*{margin:0;padding:0;box-sizing:border-box}
html,body{width:1200px;height:3734px;overflow:hidden}
body{position:relative;background:#fff;font-family:"Raleway",sans-serif;color:var(--ink)}
.backdrop{position:absolute;left:0;top:0;width:1200px;height:3734px}

/* header */
.site-header{position:absolute;left:0;top:0;width:1200px;height:108px;background:#fff}
.brand{position:absolute;left:113px;top:18px;display:flex;align-items:center;gap:10px}
.brand-dot{width:62px;height:62px;border-radius:50%;border:2px solid var(--pink-soft)}
.brand-name{font-family:"Dancing Script",cursive;font-weight:600;font-size:46px;color:var(--orange-deep);line-height:1}
.brand-tag{font-size:9px;letter-spacing:5.4px;color:var(--orange);margin-top:4px}
.nav{position:absolute;top:44px;left:445px;display:flex;gap:39px;font-size:15px;color:#444}
.btn{display:flex;align-items:center;justify-content:center;font-family:"Dancing Script",cursive;font-size:20px;color:#fff;background:var(--pink);border-radius:18px 0 18px 0}
.btn-outline{background:transparent;color:var(--pink);border:1.5px solid var(--pink)}
.book{position:absolute;left:907px;top:28px;width:180px;height:56px}

/* hero */
.hero-title{position:absolute;left:620px;top:290px;width:490px;text-align:center;font-family:"Dancing Script",cursive;font-weight:600;font-size:92px;line-height:1.1;color:var(--orange-deep)}
.hero-tag{position:absolute;left:620px;top:416px;width:490px;text-align:center;font-size:17px;letter-spacing:11px;color:var(--orange)}
.hero-btn{position:absolute;left:803px;top:480px;width:137px;height:57px}
.dots{position:absolute;left:578px;top:698px;display:flex;gap:6px}
.dots span{width:11px;height:11px;border-radius:50%;background:#ccc}
.dots span.on{background:var(--orange)}

.section-title{position:absolute;left:0;width:1200px;text-align:center;font-family:"Dancing Script",cursive;font-size:40px;font-weight:500;color:var(--pink)}

/* products */
.product{position:absolute;top:996px;width:229px;height:380px;background:#fff;box-shadow:0 2px 10px rgba(0,0,0,.12);text-align:center}
.product.active{background:var(--pink);color:#fff}
.product .photo{margin:8px;height:165px}
.product h3{font-family:"Dancing Script",cursive;font-weight:500;font-size:22px;margin-top:18px}
.product p{font-size:12.5px;line-height:21px;color:var(--muted);padding:0 22px;margin-top:12px}
.product.active p{color:#fff}
.product .btn{margin:16px auto 0;width:128px;height:52px}
.product.active .btn{border-color:#fff;color:#fff}

/* about */
.about-photo{position:absolute;left:157px;top:1625px;width:420px;height:430px;border-radius:50%;
  background:
    radial-gradient(ellipse 28% 34% at 52% 48%,#E9C9B6 0,#D9B29C 60%,transparent 100%),
    radial-gradient(ellipse 22% 18% at 38% 22%,#F3F0EE 0,transparent 100%),
    radial-gradient(ellipse 24% 20% at 60% 86%,#F1EEEC 0,transparent 100%),
    radial-gradient(ellipse 20% 16% at 70% 18%,#4A3B34 0,transparent 100%),
    linear-gradient(135deg,#9C9C9C,#7E7E80);
  border-bottom:6px solid var(--orange)}
.about-title{position:absolute;left:685px;top:1630px;font-family:"Dancing Script",cursive;font-weight:500;font-size:40px;color:var(--pink)}
.about-text{position:absolute;left:685px;top:1704px;width:398px;font-size:13.4px;line-height:25.8px;color:var(--muted);text-align:justify}
.about-btn{position:absolute;left:685px;top:1962px;width:136px;height:55px}

/* services */
.service{position:absolute;top:2365px;width:228px;height:238px;border:2px solid var(--orange);background:#fff;text-align:center}
.service svg{display:block;margin:36px auto 0}
.service h3{font-family:"Dancing Script",cursive;font-weight:500;font-size:22px;margin-top:14px}
.service p{font-size:12.5px;line-height:22px;color:var(--muted);margin-top:6px}

/* stories */
.story{position:absolute;top:2930px;width:471px;height:257px;border-radius:14px;overflow:hidden;display:flex;box-shadow:0 2px 10px rgba(0,0,0,.08)}
.story div{flex:1}
.story div+div{border-left:3px solid #fff}

/* footer */
.foot-brand{position:absolute;left:113px;top:3528px}
.foot-brand .brand-name{font-size:62px;color:var(--pink)}
.foot-brand .brand-tag{font-size:12px;letter-spacing:7.6px;margin-top:8px}
.foot-circle{position:absolute;left:200px;top:3420px;width:104px;height:104px;border-radius:50%;border:2px solid var(--pink-soft)}
.foot-col{position:absolute;top:3440px}
.foot-col h4{font-family:"Dancing Script",cursive;font-weight:500;font-size:26px;color:#222;margin-bottom:18px}
.foot-col li{list-style:none;font-size:15px;line-height:26px;color:#444}
.rule{position:absolute;left:111px;top:3640px;width:977px;height:1px;background:#ddd}
.copy{position:absolute;left:111px;top:3667px;font-size:14px;color:#333}
.social{position:absolute;left:966px;top:3667px;display:flex;gap:18px}
.social span{width:17px;height:17px;border-radius:50%;background:var(--orange)}
</style>
</head>
<body>

<svg class="backdrop" viewBox="0 0 1200 3734" aria-hidden="true">
  <defs>
    <linearGradient id="edge" x1="0" x2="1">
      <stop offset="0" stop-color="#E0338A"/>
      <stop offset=".55" stop-color="#E8556C"/>
      <stop offset="1" stop-color="#F0802C"/>
    </linearGradient>
    <radialGradient id="heroSkin" cx=".55" cy=".45" r=".5">
      <stop offset="0" stop-color="#EBCDBB"/>
      <stop offset=".6" stop-color="#DDB59F"/>
      <stop offset="1" stop-color="#DDB59F" stop-opacity="0"/>
    </radialGradient>
    <radialGradient id="glove" cx=".5" cy=".5" r=".5">
      <stop offset="0" stop-color="#F4F1EE"/>
      <stop offset="1" stop-color="#F4F1EE" stop-opacity="0"/>
    </radialGradient>
    <radialGradient id="hair" cx=".5" cy=".5" r=".5">
      <stop offset="0" stop-color="#A98B77"/>
      <stop offset="1" stop-color="#A98B77" stop-opacity="0"/>
    </radialGradient>
    <linearGradient id="storyBg" x1="0" x2="1" y1="0" y2="1">
      <stop offset="0" stop-color="#F6E3CC"/>
      <stop offset=".5" stop-color="#FBEBDB"/>
      <stop offset="1" stop-color="#F3DCC6"/>
    </linearGradient>
  </defs>

  <rect x="0" y="108" width="1200" height="730" fill="var(--hero-bg)"/>
  <g role="img" aria-label="Close-up portrait of a woman with gloved hands framing her face">
    <rect x="0" y="108" width="520" height="730" fill="#E4D9D2"/>
    <ellipse cx="200" cy="115" rx="240" ry="90" fill="url(#hair)"/>
    <ellipse cx="270" cy="420" rx="250" ry="330" fill="url(#heroSkin)"/>
    <ellipse cx="90" cy="330" rx="150" ry="130" fill="url(#glove)"/>
    <ellipse cx="330" cy="700" rx="140" ry="170" fill="url(#glove)"/>
  </g>
  <path d="M0 745 C200 840 420 840 640 770 S1050 660 1200 790 L1200 840 L0 840 Z" fill="#fff"/>
  <path d="M0 745 C200 840 420 840 640 770 S1050 660 1200 790" fill="none" stroke="url(#edge)" stroke-width="7"/>

  <path d="M0 1505 C200 1580 450 1560 700 1500 S1080 1410 1200 1510 L1200 2140 C1060 2030 850 2060 600 2130 S160 2210 0 2115 Z" fill="var(--pink-pale)"/>
  <path d="M0 1505 C200 1580 450 1560 700 1500 S1080 1410 1200 1510" fill="none" stroke="url(#edge)" stroke-width="7"/>
  <path d="M1200 2140 C1060 2030 850 2060 600 2130 S160 2210 0 2115" fill="none" stroke="url(#edge)" stroke-width="7"/>

  <g role="img" aria-label="Soft blurred spa interior with a plant in warm light">
    <path d="M0 2725 C200 2800 450 2780 700 2720 S1080 2630 1200 2730 L1200 3320 C1060 3220 850 3250 600 3320 S160 3400 0 3300 Z" fill="url(#storyBg)"/>
    <ellipse cx="1120" cy="3160" rx="80" ry="90" fill="#E8D3B4" opacity=".6"/>
  </g>
  <path d="M0 2725 C200 2800 450 2780 700 2720 S1080 2630 1200 2730" fill="none" stroke="url(#edge)" stroke-width="7"/>
  <path d="M1200 3320 C1060 3220 850 3250 600 3320 S160 3400 0 3300" fill="none" stroke="url(#edge)" stroke-width="7"/>
</svg>

<header class="site-header">
  <div class="brand">
    <span class="brand-dot"></span>
    <div>
      <div class="brand-name">Velvet Muse</div>
      <div class="brand-tag">CONCIERGE AESTHETICS</div>
    </div>
  </div>
  <nav class="nav"><span>Home</span><span>About</span><span>Services</span><span>Products</span><span>Stories</span></nav>
  <a class="btn book">Book Appointment</a>
</header>

<div class="hero-title">Velvet Muse</div>
<div class="hero-tag">CONCIERGE AESTHETICS</div>
<a class="btn hero-btn">Get Started</a>
<div class="dots"><span></span><span class="on"></span><span></span></div>

<h2 class="section-title" style="top:912px">Our Products</h2>

<div class="product" style="left:111px">
  <div class="photo" role="img" aria-label="Aesthetician treating a client in a bright studio" style="background:radial-gradient(ellipse 30% 45% at 25% 45%,#F7F5F3,transparent),radial-gradient(ellipse 30% 25% at 60% 75%,#C9A38D,transparent),linear-gradient(135deg,#E9E6E2,#C9BFB6)"></div>
  <h3>Lorem ipsum dolor</h3>
  <p>Lorem ipsum dolor sit amet, consectetur adipiscing elit, sed aliqua.</p>
  <a class="btn btn-outline">View Details</a>
</div>
<div class="product active" style="left:359px">
  <div class="photo" role="img" aria-label="Client relaxing during a facial treatment" style="background:radial-gradient(ellipse 35% 30% at 50% 55%,#E2BFA8,transparent),radial-gradient(ellipse 30% 25% at 70% 20%,#F0E8E2,transparent),linear-gradient(135deg,#F4F0EE,#D8C8BE)"></div>
  <h3>Lorem ipsum dolor</h3>
  <p>Lorem ipsum dolor sit amet, consectetur adipiscing elit, sed aliqua.</p>
  <a class="btn btn-outline">View Details</a>
</div>
<div class="product" style="left:609px">
  <div class="photo" role="img" aria-label="Smiling client during a skin consultation" style="background:radial-gradient(ellipse 28% 45% at 68% 45%,#D8A58A,transparent),radial-gradient(ellipse 25% 40% at 80% 30%,#4B3328,transparent),linear-gradient(135deg,#5FB0B8,#8CC5C7)"></div>
  <h3>Lorem ipsum dolor</h3>
  <p>Lorem ipsum dolor sit amet, consectetur adipiscing elit, sed aliqua.</p>
  <a class="btn btn-outline">View Details</a>
</div>
<div class="product" style="left:858px">
  <div class="photo" role="img" aria-label="Client in a towel receiving a face massage" style="background:radial-gradient(ellipse 30% 30% at 50% 50%,#E8BFA2,transparent),radial-gradient(ellipse 30% 20% at 50% 18%,#FAF7F5,transparent),linear-gradient(135deg,#F1E9E4,#DDBFA8)"></div>
  <h3>Lorem ipsum dolor</h3>
  <p>Lorem ipsum dolor sit amet, consectetur adipiscing elit, sed aliqua.</p>
  <a class="btn btn-outline">View Details</a>
</div>

<div class="about-photo" role="img" aria-label="Portrait of a woman with gloved hands touching her face"></div>
<h2 class="about-title">About Us</h2>
<p class="about-text">Sed ut perspiciatis unde omnis iste natus error sit voluptatem accu santium doloremque laudantium, totam rem aperiam, eaque ipsa quae ab illo inventore veritatis et quasi architecto beatae vitae dicta sunt explicabo. Nemo enim ipsam voluptatem quia voluptas sit aspernatur aut odit aut fugit, sed quia consequuntur magni dolores eos qui ratione voluptatem sequi nesciunt. Neque porro quisquam est, qui dolorem ipsum quia dolor sit amet, consectetur, adipisci velit, sed quia non magnam aliquam quaerat voluptatem.</p>
<a class="btn about-btn">Get Started</a>

<h2 class="section-title" style="top:2264px">Our Services</h2>

<div class="service" style="left:223px">
  <svg width="60" height="70" viewBox="0 0 60 70" fill="none" stroke="var(--pink)" stroke-width="3"><circle cx="30" cy="18" r="13"/><path d="M6 66 V56 a20 20 0 0 1 48 0 V66 Z"/></svg>
  <h3>Private Session</h3>
  <p>Lorem ipsum dolor sit amet,<br>consectetur adipiscing</p>
</div>
<div class="service" style="left:486px">
  <svg width="96" height="70" viewBox="0 0 96 70" fill="none" stroke="var(--pink)" stroke-width="3"><circle cx="18" cy="24" r="10"/><circle cx="48" cy="18" r="12"/><circle cx="78" cy="24" r="10"/><path d="M2 62 V54 a16 16 0 0 1 26 -12"/><path d="M94 62 V54 a16 16 0 0 0 -26 -12"/><path d="M26 64 V54 a22 22 0 0 1 44 0 V64 Z"/></svg>
  <h3>Group Session</h3>
  <p>Lorem ipsum dolor sit amet,<br>consectetur adipiscing</p>
</div>
<div class="service" style="left:749px">
  <svg width="96" height="80" viewBox="0 0 96 80" fill="none" stroke="var(--pink)" stroke-width="3"><circle cx="33" cy="11" r="8"/><circle cx="63" cy="11" r="8"/><circle cx="16" cy="32" r="9"/><circle cx="80" cy="32" r="9"/><circle cx="48" cy="30" r="11"/><path d="M2 72 V64 a15 15 0 0 1 24 -12"/><path d="M94 72 V64 a15 15 0 0 0 -24 -12"/><path d="M26 76 V64 a22 22 0 0 1 44 0 V76 Z"/></svg>
  <h3>Party</h3>
  <p>Lorem ipsum dolor sit amet,<br>consectetur adipiscing</p>
</div>

<h2 class="section-title" style="top:2832px">Our Stories</h2>

<div class="story" style="left:111px" role="img" aria-label="Before and after comparison of a client's facial skin">
  <div style="background:radial-gradient(ellipse 40% 50% at 85% 45%,#DDB49C,transparent),radial-gradient(ellipse 45% 30% at 45% 80%,#F2EFEC,transparent),linear-gradient(135deg,#E9E3DE,#CDB7A8)"></div>
  <div style="background:radial-gradient(ellipse 45% 55% at 20% 45%,#D9B7A3,transparent),linear-gradient(135deg,#E4DDD8,#F0EEEC)"></div>
</div>
<div class="story" style="left:617px" role="img" aria-label="Before and after comparison of the skin around a client's eyes">
  <div style="background:radial-gradient(ellipse 25% 18% at 45% 45%,#6F6A68,transparent),linear-gradient(135deg,#CFAE9E,#B08D7E)"></div>
  <div style="background:radial-gradient(ellipse 25% 18% at 50% 45%,#6F6A68,transparent),linear-gradient(135deg,#DCC2B4,#C7A796)"></div>
</div>

<span class="foot-circle"></span>
<div class="foot-brand">
  <div class="brand-name">Velvet Muse</div>
  <div class="brand-tag">CONCIERGE AESTHETICS</div>
</div>

<div class="foot-col" style="left:486px">
  <h4>Quick Links</h4>
  <ul><li>Home</li><li>About</li><li>Services</li><li>Products</li><li>Stories</li></ul>
</div>
<div class="foot-col" style="left:725px">
  <h4>Service</h4>
  <ul><li>Private Session</li><li>Group Session</li><li>Party</li></ul>
</div>
<div class="foot-col" style="left:950px">
  <h4>Conditions</h4>
  <ul><li>Delivery</li><li>Terms of Conditions</li><li>Privacy policy</li></ul>
</div>

<div class="rule"></div>
<p class="copy">Copyrights 2022 Velvet Muse &nbsp;|&nbsp;&nbsp; All Rights Reserved</p>
<div class="social" aria-label="Social links"><span></span><span></span><span></span><span></span></div>

</body>
</html>
```